Business Card Design for company

We want new business cards. We'd like something different-- yet still highly professional. Our tagline is Providing leadership, delivering success. Stock photos are ok, as long as they are relevant and look upscale.

Target Market(s)

Architecture/Business Management Consulting/Engineering Consulting

Contact Information for Business Card

dark gray background with pops of blue might be good, but you tell me. You're the designers. Rounded corners might be nice, but again, you tell me.

Font styles to use
Serif
Sans Serif

Colors
3276b5
5c5c5c
9d9d9d
fbfbfb

Requirements
Nice to have
• Something different, but still very professional.

```html
<!DOCTYPE html>
<html lang="en">
<head>
<meta charset="utf-8">
<title>Norvale Advisory – Business Cards</title>
<link href="https://fonts.googleapis.com/css2?family=Roboto:wght@400;500;700&display=swap" rel="stylesheet">
<style>
  :root {
    --stage: #2e2f31;
    --card-dark: #4a4d55;
    --card-light: #fbfbfb;
    --brand-blue: #3276b5;
    --text-gray: #5c5c5c;
    --soft-gray: #9d9d9d;
    --white: #ffffff;
  }
  * { margin: 0; padding: 0; box-sizing: border-box; }
  html, body {
    width: 1200px; height: 768px; overflow: hidden;
    background: var(--stage);
    font-family: "Roboto", Arial, sans-serif;
  }
  .canvas {
    width: 1200px; height: 768px;
    display: flex; align-items: center; justify-content: center; gap: 40px;
  }
  .card {
    width: 540px; height: 309px;
    border-radius: 6px;
    position: relative;
    box-shadow: 0 10px 30px rgba(0,0,0,0.45);
  }
  /* Back of card */
  .card-back {
    background: var(--card-dark);
    display: flex; flex-direction: column; align-items: center; justify-content: center;
    color: var(--white);
  }
  .card-back .brand-name {
    font-size: 40px; font-weight: 700; letter-spacing: 2px;
    color: var(--white);
  }
  .card-back .tagline {
    position: absolute; bottom: 42px; left: 0; right: 0;
    text-align: center; font-size: 13px; letter-spacing: 0.6px; color: var(--white);
  }
  /* Front of card */
  .card-front {
    background: var(--card-light);
    display: flex; align-items: center;
    padding: 0 34px 0 38px;
  }
  .brand-block {
    flex: 0 0 230px;
    display: flex; align-items: center; gap: 12px;
  }
  .brand-mark {
    width: 18px; height: 18px; background: var(--brand-blue); flex: 0 0 auto;
  }
  .brand-block .brand-name {
    font-size: 26px; font-weight: 700; line-height: 1.1;
    color: var(--brand-blue); text-transform: uppercase; letter-spacing: 1px;
  }
  .contact-block {
    flex: 1; padding-left: 30px;
    color: var(--text-gray);
  }
  .person-name {
    font-size: 19px; font-weight: 700; color: var(--brand-blue);
    text-transform: uppercase; letter-spacing: 0.5px;
  }
  .person-title {
    font-size: 12px; font-weight: 500; text-transform: uppercase;
    letter-spacing: 0.4px; margin-bottom: 18px;
  }
  .address { font-size: 12.5px; line-height: 1.35; margin-bottom: 8px; }
  .contact-list { list-style: none; font-size: 12.5px; line-height: 1.4; margin-bottom: 12px; }
  .contact-list .label { color: var(--brand-blue); font-weight: 700; margin-right: 4px; }
  .website {
    font-size: 14px; font-weight: 700; color: var(--brand-blue); letter-spacing: 0.8px;
  }
</style>
</head>
<body>
<main class="canvas">
  <section class="card card-back" aria-label="Card back">
    <div class="brand-name">NORVALE</div>
    <p class="tagline">Providing leadership, delivering success</p>
  </section>

  <section class="card card-front" aria-label="Card front">
    <div class="brand-block">
      <span class="brand-mark"></span>
      <div class="brand-name">Norvale<br>Advisory</div>
    </div>
    <div class="contact-block">
      <h1 class="person-name">Daniel Reeve</h1>
      <p class="person-title">CEO/Founder</p>
      <p class="address">4120 Cedar Ridge Road<br>Juneau, Alaska 99801</p>
      <ul class="contact-list">
        <li><span class="label">P :</span>907 555 0142</li>
        <li><span class="label">M :</span>907 555 0187</li>
        <li><span class="label">F :</span>907 555 0163</li>
        <li><span class="label">E :</span>daniel@norvaleadvisory.com</li>
      </ul>
      <p class="website">www.norvaleadvisory.com</p>
    </div>
  </section>
</main>
</body>
</html>
```